Harrow Grading LLC business card design

Excavation company business cards

Contact Information for Business Card

Harrow Grading LLC cell phone 208-417-6290 office phone 208-319-4856 harrowgradingllc@maplecove.com Driveways, site prep, retaining walls, septic systems, rock delivery

Colors

Designer to choose colors to be used in the design.

```html
<!DOCTYPE html>
<html lang="en">
<head>
<meta charset="utf-8">
<title>Harrow Grading LLC – Business Card</title>
<link rel="stylesheet" href="https://fonts.googleapis.com/css2?family=Oswald:wght@500&family=Lato:wght@400;700&family=Arimo:wght@400&display=swap">
<style>
  :root {
    --backdrop: #1d1d1d;
    --card: #121212;
    --orange: #ec6f1f;
    --grey: #8c8c8c;
    --grey-soft: #6e6e6e;
  }
  * { box-sizing: border-box; margin: 0; padding: 0; }
  html, body {
    width: 1200px;
    height: 900px;
    overflow: hidden;
    background: var(--backdrop);
  }
  .canvas {
    position: relative;
    width: 1200px;
    height: 900px;
  }
  .card {
    position: absolute;
    left: 290px;
    width: 620px;
    height: 354px;
    background: var(--card);
    box-shadow: 0 10px 24px rgba(0, 0, 0, 0.55);
    overflow: hidden;
  }
  .card--front { top: 60px; }
  .card--back { top: 466px; }
  .card__band {
    position: absolute;
    left: 0;
    right: 0;
    bottom: 0;
    height: 13px;
    background: var(--orange);
  }

  /* Front */
  .brand {
    position: absolute;
    top: 112px;
    left: 0;
    right: 0;
    display: flex;
    align-items: center;
    justify-content: center;
    gap: 14px;
  }
  .brand__mark {
    width: 22px;
    height: 22px;
    background: var(--orange);
  }
  .brand__name {
    font-family: "Lato", sans-serif;
    font-weight: 700;
    font-size: 38px;
    letter-spacing: 1px;
    color: var(--orange);
  }
  .services {
    position: absolute;
    top: 196px;
    left: 0;
    right: 0;
    text-align: center;
    font-family: "Arimo", sans-serif;
    font-size: 19px;
    line-height: 26px;
    color: var(--grey);
  }
  .services__dot {
    display: inline-block;
    width: 9px;
    height: 9px;
    margin: 0 6px 2px;
    border-radius: 50%;
    background: var(--orange);
    vertical-align: middle;
  }

  /* Back */
  .person {
    position: absolute;
    top: 120px;
    left: 70px;
    width: 200px;
    text-align: right;
  }
  .person__name {
    font-family: "Oswald", sans-serif;
    font-weight: 500;
    font-size: 32px;
    line-height: 38px;
    color: var(--orange);
    text-transform: uppercase;
    letter-spacing: -0.3px;
  }
  .person__title {
    font-family: "Lato", sans-serif;
    font-size: 18px;
    color: var(--grey);
  }
  .divider {
    position: absolute;
    top: 124px;
    left: 296px;
    width: 1px;
    height: 66px;
    background: var(--grey-soft);
  }
  .phones {
    position: absolute;
    top: 130px;
    left: 322px;
    list-style: none;
    font-family: "Arimo", sans-serif;
    font-size: 19px;
    color: var(--grey);
  }
  .phones__item {
    display: flex;
    align-items: center;
    gap: 12px;
    height: 28px;
  }
  .phones__icon {
    width: 18px;
    height: 18px;
    flex: none;
  }
  .email {
    position: absolute;
    top: 262px;
    left: 84px;
    font-family: "Arimo", sans-serif;
    font-size: 18px;
    color: var(--grey);
  }
  .email__label { color: var(--orange); margin-right: 4px; }
</style>
</head>
<body>
<main class="canvas">

  <section class="card card--front" aria-label="Card front">
    <div class="brand">
      <span class="brand__mark"></span>
      <span class="brand__name">Harrow Grading LLC</span>
    </div>
    <p class="services">
      Driveways<span class="services__dot"></span>Site prep<span class="services__dot"></span>Retaining walls<br>
      Septic systems<span class="services__dot"></span>Rock delivery
    </p>
    <div class="card__band"></div>
  </section>

  <section class="card card--back" aria-label="Card back">
    <div class="person">
      <h1 class="person__name">Marcus Hale</h1>
      <p class="person__title">Managing Director</p>
    </div>
    <div class="divider"></div>
    <ul class="phones">
      <li class="phones__item">
        <svg class="phones__icon" viewBox="0 0 18 18" aria-hidden="true">
          <rect x="4" y="1.5" width="10" height="15" rx="2" fill="none" stroke="var(--orange)" stroke-width="1.8"/>
          <line x1="7.5" y1="13.5" x2="10.5" y2="13.5" stroke="var(--orange)" stroke-width="1.6"/>
        </svg>
        <span>208-417-6290</span>
      </li>
      <li class="phones__item">
        <svg class="phones__icon" viewBox="0 0 18 18" aria-hidden="true">
          <path d="M4 2.5 L7 2 L8 6 L6 7.2 C6.8 9.2 8.5 11 10.6 12 L11.8 10 L15.8 11 L15.5 14 C15.3 15.2 14.3 16 13 15.8 C7.8 15 3 10.2 2.2 5 C2 3.7 2.8 2.7 4 2.5 Z" fill="var(--orange)"/>
        </svg>
        <span>208-319-4856</span>
      </li>
    </ul>
    <p class="email"><span class="email__label">E:</span>harrowgradingllc@maplecove.com</p>
    <div class="card__band"></div>
  </section>

</main>
</body>
</html>
```